Software Development Consulting Company Needs Business Card Design

We need a new business card design for our consultants at Kestrel Works (kestrelworks.example). We are a small firm that provides high-end software development and methodology consulting to medium to large enterprise IT organizations.

Our logo uses Futura for the font and we would like to stick with navy blue and canary yellow for the logo colors. Attached are normal and reversed versions of our logos in illustrator format.
Updates

Hi Everyone, Thank yo very much for your amazing design ideas. I have created a poll for this project and our employees will be voting on the design they wish to use. We will be making a decision this Wednesday (October 22nd). Thanks again, Dale Hartwick

Industry/Entity Type

Business

```html
<!DOCTYPE html>
<html lang="en">
<head>
<meta charset="utf-8">
<title>Kestrel Works — Business Card</title>
<link rel="stylesheet" href="https://fonts.googleapis.com/css2?family=Jost:wght@400;500&family=Open+Sans:wght@400;600;700&display=swap">
<style>
  :root {
    --navy: #1d4a73;
    --canary: #ffec00;
    --paper: #ffffff;
    --backdrop: #e9e6e1;
    --ink-muted: #7a7f86;
    --url-ink: #4b5560;
  }
  * { box-sizing: border-box; margin: 0; padding: 0; }
  html, body { width: 1200px; height: 720px; overflow: hidden; }
  body {
    background: var(--backdrop);
    font-family: "Open Sans", Arial, sans-serif;
    position: relative;
  }
  .card {
    position: absolute;
    width: 525px;
    height: 300px;
    overflow: hidden;
    box-shadow: 0 10px 24px rgba(0,0,0,0.18);
  }
  .card--front { left: 50px; top: 210px; background: var(--paper); }
  .card--back  { left: 625px; top: 210px; background: var(--canary); }

  .card__waves { position: absolute; inset: 0; width: 100%; height: 100%; }

  .brand {
    position: absolute;
    display: flex;
    align-items: center;
    gap: 10px;
    font-family: "Jost", "Futura", sans-serif;
    font-weight: 500;
    color: var(--navy);
    letter-spacing: 0.1em;
    text-transform: uppercase;
    white-space: nowrap;
    line-height: 1;
  }
  .brand__dot {
    border: 3px solid var(--navy);
    border-radius: 50%;
    flex: none;
  }
  .card--front .brand { left: 30px; top: 78px; font-size: 22px; }
  .card--front .brand__dot { width: 26px; height: 26px; }

  .holder { position: absolute; left: 48px; top: 178px; }
  .holder__name { font-size: 15px; font-weight: 700; color: var(--navy); }
  .holder__title { font-size: 11px; color: var(--ink-muted); margin-top: 1px; }

  .contact {
    position: absolute;
    right: 24px;
    top: 94px;
    list-style: none;
    color: var(--paper);
    font-size: 12.5px;
    line-height: 24px;
  }
  .contact__item { display: flex; justify-content: flex-end; align-items: center; gap: 7px; white-space: nowrap; }
  .contact__icon { width: 12px; height: 12px; flex: none; display: block; }
  .contact__item--place { margin-top: 3px; }

  .card--back .brand {
    left: 50%; top: 110px; transform: translateX(-50%);
    font-size: 30px;
  }
  .card--back .brand__dot { width: 34px; height: 34px; }
  .back__url {
    position: absolute;
    left: 0; right: 0; top: 218px;
    text-align: center;
    font-size: 15px;
    letter-spacing: 0.26em;
    color: var(--url-ink);
  }
</style>
</head>
<body>
  <section class="card card--front" aria-label="Business card front">
    <svg class="card__waves" viewBox="0 0 525 300" preserveAspectRatio="none" aria-hidden="true">
      <path transform="translate(-14,-14)" d="M0,262 C120,258 230,200 270,130 C305,70 390,44 525,36" fill="none" stroke="var(--navy)" stroke-width="2.5"/>
      <path transform="translate(-5,-6)" d="M0,262 C120,258 230,200 270,130 C305,70 390,44 525,36" fill="none" stroke="var(--canary)" stroke-width="8"/>
      <path d="M0,264 C120,260 232,202 272,132 C307,72 392,46 525,40 L525,300 L0,300 Z" fill="var(--navy)"/>
    </svg>

    <div class="brand"><span class="brand__dot"></span>Kestrel Works</div>

    <div class="holder">
      <p class="holder__name">Your Name</p>
      <p class="holder__title">Title</p>
    </div>

    <ul class="contact">
      <li class="contact__item">
        <svg class="contact__icon" viewBox="0 0 12 12" aria-hidden="true"><circle cx="6" cy="6" r="5.5" fill="none" stroke="#fff"/><path d="M4,3 L5,3 L5.5,4.5 L4.8,5 C5.2,6 6,6.8 7,7.2 L7.5,6.5 L9,7 L9,8 C6,8.5 3.5,6 4,3 Z" fill="#fff"/></svg>
        <span>555-014-2290</span>
      </li>
      <li class="contact__item">
        <svg class="contact__icon" viewBox="0 0 12 12" aria-hidden="true"><circle cx="6" cy="6" r="6" fill="#fff"/><rect x="3" y="4" width="6" height="4.2" fill="var(--navy)"/><path d="M3,4 L6,6.3 L9,4" fill="none" stroke="#fff" stroke-width="0.8"/></svg>
        <span>info@kestrelworks.example</span>
      </li>
      <li class="contact__item">
        <svg class="contact__icon" viewBox="0 0 12 12" aria-hidden="true"><circle cx="6" cy="6" r="6" fill="#fff"/><circle cx="6" cy="6" r="3.6" fill="none" stroke="var(--navy)" stroke-width="0.8"/><path d="M2.4,6 H9.6 M6,2.4 V9.6" stroke="var(--navy)" stroke-width="0.8"/></svg>
        <span>www.kestrelworks.example</span>
      </li>
      <li class="contact__item contact__item--place"><span>Northfield + Ashby, IL</span></li>
    </ul>
  </section>

  <section class="card card--back" aria-label="Business card back">
    <div class="brand"><span class="brand__dot"></span>Kestrel Works</div>
    <p class="back__url">www.kestrelworks.example</p>
  </section>
</body>
</html>
```